Dentistry Office

We want a new design for a Dentist's office website.

The theme is: "We provide high quality, state-of-the-art, dental care in a comfortable, caring environment."

The site currently has a menu on the left of the page with about 40 items on it. There is a great deal of textual content on each page, plus several illustrations.

We want to do this using CSS, so we need specifications in the CSS for all possible elements. The CSS needs to be named in a logical manner for easy use.

Every dentist on the planet seems to use lots of Flash. We don't want to because it is so distracting. We are looking for an elegant solution targeting 24-55 age group, but not excluding anyone.

The following (from another dentist's site) can give you a taste of what we want to communicate on the site:

"After 20 years of teaching dentists how to refine their technique and many years of writing textbooks, I currently devote my time to my office and the hands-on practice of dentistry. I'd like to welcome you personally to my dental practice, and I invite you to meet my highly experienced team of professionals.

"We have offered complete dental care of the highest quality since 1978. We provide Preventive Services, Tooth Whitening and Cosmetic Dentistry for a beautiful smile, Endodontics (root canal treatment) to treat painful teeth, Sedation Dentistry so you can relax, and Dental Implants to restore what is missing. We offer total care.

"Our approach to your health is simple: We use our education, experience and dedication to provide every patient with superior dental care.

"This passion for excellence is not just a goal, but a standard every member of our team holds.

"We also pride ourselves with our state of the art procedures, training and technology. This includes creating a beautiful smile using techniques that preserve as much of the original tooth as possible.

"Our abilities are renowned throughout the dental profession and I hope if you have any questions you will contact us by an e-mail note, by phone or just by dropping by."

Keep in mind the screen shape and dimensions. Your design needs to work in the normal screen proportions, regardless of how it looks when you post it here. Scrolling is OK, but the first impression needs to work.
Updates

Keep in mind that there will be about 250 words, or more, on each page.

Competitors web sites:

http://www.brindlecovedentist.example/

http://www.brindlecovedentalcare.example/

http://www.grinsbymarlowvaledental.example/

http://www.tenbyfamilydentalcare.example/

http://www.quelmardental.example/

http://www.dovrinadental.example/

We need to compete with these.

Target Market(s)

Generally adults seeking the most experienced and comfortable-to-be-with dentist.

Industry/Entity Type

Training

Requirements
Must have
• Must stand apart from other dentists.
• Must be elegant.
• Must have a horizontal menu structure across all columns, NOT a vertical that requires scrolling, no popout, pop down, etc. menus.
• We are looking for something special.
• Do not waste your time or ours putting up templates and things you have used before.
• Personally, I do not see how someone outside the US can understand the northern California dental market. But you are welcome to try.
Should not have
• Flash or graphics that move
• The look of a template
• Folksy fonts
• Looks like you used it 20 times before

```html
<!DOCTYPE html>
<html lang="en">
<head>
<meta charset="utf-8">
<title>Dentist's Office</title>
<link rel="stylesheet" href="https://fonts.googleapis.com/css2?family=Arimo:wght@400;700&display=swap">
<style>
:root{
  --orange:#f07d00;
  --orange-bright:#ff9a1a;
  --orange-soft:#fbb04a;
  --text:#555555;
  --text-dark:#333333;
  --heading:#666666;
  --rule:#d6d6d6;
  --canvas:#d9d9d9;
  --page:#ffffff;
  --footer-bg:#e9e9ea;
  --white:#ffffff;
}
*{box-sizing:border-box;margin:0;padding:0}
html,body{width:1200px;height:900px;overflow:hidden}
body{background:var(--canvas);font-family:"Arimo",Arial,sans-serif;color:var(--text);position:relative}
ul{list-style:none}
a{color:inherit;text-decoration:none}

.page{position:absolute;left:115px;top:52px;width:971px;height:836px;background:linear-gradient(#ffffff 0,#eeeeee 113px,#ffffff 114px,#f1f1f1 139px,#ffffff 330px);overflow:hidden}

/* header */
.brand{position:absolute;left:71px;top:40px;display:flex;align-items:center;gap:10px}
.brand-mark{width:42px;height:42px;border-radius:8px;background:var(--orange)}
.brand-name{font-size:28px;color:var(--text-dark);letter-spacing:-.8px}
.util-nav{position:absolute;left:757px;top:29px;display:flex;gap:16px;font-size:11px;color:var(--text-dark)}
.util-nav a::before,.crumbs li::before{content:"";display:inline-block;border-left:5px solid var(--orange);border-top:3px solid transparent;border-bottom:3px solid transparent;margin-right:3px;vertical-align:1px}
.search{position:absolute;left:757px;top:67px;width:172px;height:17px;border:1px solid #bdbdbd;background:var(--white);font-size:11px;color:#9a9a9a;padding:2px 7px;box-shadow:inset 0 1px 2px rgba(0,0,0,.12)}
.search svg{position:absolute;right:6px;top:2px}

/* main nav: flat horizontal menu, no drop-downs */
.main-nav{position:absolute;left:0;top:113px;width:971px;height:26px;background:linear-gradient(var(--orange-bright) 0,var(--orange-bright) 60%,var(--orange) 61%,#f59a2c 100%)}
.main-nav ul{display:flex;position:absolute;left:77px;top:0;height:26px;font-size:13.5px;color:var(--white)}
.main-nav li{line-height:27px;margin-right:36px}
.main-nav li.is-current{margin-left:-16px;margin-right:24px;padding:0 12px 0 6px;color:var(--text-dark);background:#fbae4c;border-radius:6px 6px 0 0}

/* content */
.crumbs{position:absolute;left:77px;top:183px;display:flex;gap:10px;font-size:9.5px;color:#777}
.crumbs li::before{border-left-color:#777}
.crumbs li.current{color:var(--orange)}
.crumbs li.current::before{border-left-color:var(--orange)}
.page-title{position:absolute;left:73px;top:212px;font-size:24.7px;font-weight:400;color:var(--heading)}
.lead{position:absolute;left:74px;top:258px;width:640px;font-size:15.8px;color:var(--orange);line-height:28.5px}
.lead span{border-bottom:1px solid var(--rule);display:inline;padding-bottom:5px}
.body-col{position:absolute;top:361px;font-size:11.4px;line-height:21px;color:var(--text)}
.body-col.first{left:75px;width:330px}
.body-col.second{left:421px;width:290px}
.body-col a{color:var(--orange)}
.photo{float:left;width:112px;height:95px;margin:6px 28px 6px 3px;border-radius:7px;background:var(--white);padding:5px;box-shadow:0 1px 5px rgba(0,0,0,.3)}
.photo div{width:100%;height:100%;border-radius:4px;background:linear-gradient(135deg,#c9706c,#e8c8c0 55%,#b9514e)}

/* sidebar */
.sidebar{position:absolute;left:745px;top:139px;width:192px;height:509px;background:var(--white);box-shadow:0 0 6px rgba(0,0,0,.25);font-size:11px;color:var(--text-dark)}
.tools{position:absolute;left:15px;top:115px;line-height:21px}
.tools li{display:flex;align-items:center;gap:9px}
.side-title{position:absolute;left:15px;font-size:13px;font-weight:700;color:#444}
.side-list{position:absolute;left:15px;line-height:24px}
.side-list.archive{line-height:22px}
.side-list li,.footer-col li{display:flex;align-items:center;gap:9px}
.dot{width:10px;height:10px;border-radius:50%;background:var(--orange);position:relative;flex:none}
.dot::after{content:"";position:absolute;left:4px;top:3px;border-left:3px solid var(--white);border-top:2px solid transparent;border-bottom:2px solid transparent}

/* footer */
.footer-bar{position:absolute;left:0;top:650px;width:971px;height:26px;background:linear-gradient(var(--orange-bright) 0,var(--orange-bright) 50%,var(--orange) 51%);font-size:10.5px;color:var(--white);text-align:center;line-height:28px}
.footer-bar .sep{margin:0 7px;color:#ffd49a}
.footer-bar .copy{margin-right:17px}
.footer{position:absolute;left:0;top:676px;width:971px;height:160px;background:linear-gradient(#dadadb,var(--footer-bg) 20%,#fafafa)}
.footer-col{position:absolute;font-size:11px;color:var(--text);line-height:17px}
.footer-col h3{font-size:13px;color:var(--orange);font-weight:700;margin-bottom:8px}
.footer-col .dot{background:#555;width:9px;height:9px}
.footer-col .dot::after{left:3px;top:2.5px}
.footer-col .label{color:var(--orange);font-weight:700}
.footer-col .mail{color:var(--orange)}
</style>
</head>
<body>
<div class="page">
  <header>
    <div class="brand"><span class="brand-mark"></span><span class="brand-name">Dentist's Office</span></div>
    <nav class="util-nav"><a href="#">home</a><a href="#">sitemap</a><a href="#">contact</a></nav>
    <div class="search">search...
      <svg width="12" height="12" viewBox="0 0 12 12"><circle cx="5" cy="5" r="3.6" fill="none" stroke="#999" stroke-width="1.5"/><line x1="7.6" y1="7.6" x2="11" y2="11" stroke="#999" stroke-width="1.8"/></svg>
    </div>
  </header>

  <nav class="main-nav">
    <ul>
      <li>home</li><li>about us</li><li>services</li><li>menu item</li>
      <li>menu item</li><li class="is-current">menu item</li><li>contact</li>
    </ul>
  </nav>

  <ul class="crumbs"><li>home</li><li>parent page</li><li class="current">current page</li></ul>
  <h1 class="page-title">Lorem ipsum dolar sit amet elit nam in</h1>
  <p class="lead"><span>Lorem ipsum dolor sit amet, consectetur adipiscing elit. Etiam hendrerit fringilla sodales.</span><br><span>Nulla pretium mattis mollis. Pellentesque eu tortor massa, vel lacinia libero. Nam in justo</span><br><span>non odio luctus iaculis sit amet vitae dolor. Morbi varius.</span></p>

  <div class="body-col first">
    <div class="photo"><div role="img" aria-label="Photo of a smiling mouth with a hand fitting a clear dental aligner"></div></div>
    In scelerisque magna nulla ut nunc. Aliquam erat volutpat. Donec at libero eros, vitae accumsan velit. Nam eu neque dolor. Nullam <a href="#">imperdiet quam sit amet</a> eros luctus id dignissim nulla tempus.<br>
    Lorem vestibulum in massa ac ipsum pharetra faucibus. dignis-sim nulla tempus. dignissim nulla tempus. In scelerisque magna nulla ut nunc. Aliquam erat volutpat. Donec at libero eros, vitae accumsan velit. Nam eu neque dolor. Nullam<br>
    Lorem vestibulum in massa ac ipsum pharetra faucibus.
  </div>
  <div class="body-col second">
    Quisque convallis erat urna, sit amet feugiat massa. Aenean auctor mauris id arcu venenatis tincidunt. Viva-mus sollicitudin tincidunt suscipit. Phasellus lobortis magna eu mi lacinia ac dapibus ligula mattis. Phasellus malesuada nisi non nunc rutrum pellentesque. In porta hendrerit odio, ut vulputate urna tincidunt quis. Nulla malesuada tellus non lacus blandit gravida nec u<br>
    In scelerisque magna nulla ut nunc. Aliquam erat volut-pat. Donec at libero eros, vitae accumsan velit. Nam eu neque dolor. Nullam In scelerisque magna nulla ut nunc. Aliquam erat volutpat. Donec at libero eros.
  </div>

  <aside class="sidebar">
    <ul class="tools">
      <li><svg width="14" height="12" viewBox="0 0 14 12"><rect x="3" y="0" width="8" height="4" fill="#444"/><rect x="0" y="4" width="14" height="5" rx="1" fill="#444"/><rect x="3" y="7" width="8" height="5" fill="#fff" stroke="#444"/></svg>print this page</li>
      <li><svg width="14" height="10" viewBox="0 0 14 10"><rect width="14" height="10" fill="#444"/><path d="M0 0 L7 6 L14 0" fill="none" stroke="#fff" stroke-width="1.2"/></svg>e-mail this page</li>
    </ul>
    <h2 class="side-title" style="top:191px">Recent news</h2>
    <ul class="side-list" style="top:221px"><li><span class="dot"></span>lorem ipsum</li><li><span class="dot"></span>lorem ipsum dolar</li><li><span class="dot"></span>lorem ipsum</li></ul>
    <h2 class="side-title" style="top:317px">Archive</h2>
    <ul class="side-list archive" style="top:344px"><li><span class="dot"></span>june</li><li><span class="dot"></span>april</li><li><span class="dot"></span>2009</li></ul>
  </aside>

  <div class="footer-bar"><span class="copy">(c) 2010 Dentist's Office All rights reserved</span>Privacy Policy<span class="sep">|</span>Security Statement<span class="sep">|</span>Contact</div>
  <footer class="footer">
    <div class="footer-col" style="left:77px;top:33px"><h3>About Dentist's Office</h3><ul><li><span class="dot"></span>lorem ipsum dolar sit</li><li><span class="dot"></span>lorem ipsum dolar sit</li><li><span class="dot"></span>lorem ipsum dolar sit</li></ul></div>
    <div class="footer-col" style="left:306px;top:27px"><h3>Services</h3><ul><li><span class="dot"></span>lorem ipsum dolar sit</li><li><span class="dot"></span>lorem ipsum dolar sit</li><li><span class="dot"></span>lorem ipsum dolar sit</li></ul></div>
    <div class="footer-col" style="left:532px;top:27px"><h3>Address</h3>1840 Harrow Lane<br>Quelmar, VA 23900-0000</div>
    <div class="footer-col" style="left:757px;top:39px"><span class="label">T</span> 0100 555 014<br><span class="label">F</span> 0100 555 015<br><span class="mail">hello@dentistsoffice.example</span></div>
  </footer>
</div>
</body>
</html>
```